Willow Creek Gatherings Event Planning in need of a design!!

Event Planning company, does a variety of events. I like simple more rustic designs focused on almond blossoms. We are based out of Northern California, the heart of almond country. I would like to see colors in light pinks, beige, light browns, whites or creams. the final design should communicate rustic simplicity. Below are some pictures of Almond blossoms and design ideas I prefer the one called Tulip Grove. Thanks

Target Market(s)

Women in the mid twenties and older. They should be in the upper middle class in need of an amazing party design and coordinator

Industry/Entity Type

Event Planning

Contact Information for Business Card

Maren Lockwood 530-624-0295almondbaffairs@gmail.comalmondblossomaffairs.com

Font styles to use
Other font styles liked:
• Amatic SC

Requirements
Must have
• almond blossom
• my information
• simplicity
Nice to have
• rustic design
• vintage feel
• whimsical
Should not have
• i like pink but not over the top

```html
<!DOCTYPE html>
<html lang="en">
<head>
<meta charset="utf-8">
<title>Willow Creek Gatherings – Business Card</title>
<link href="https://fonts.googleapis.com/css2?family=Open+Sans:wght@400;600;700&display=swap" rel="stylesheet">
<style>
  :root {
    --page-bg: #efebe6;
    --card-cream: #fdfbf7;
    --brand-rose: #a8687b;
    --band-rose: #c48f9d;
    --rule-brown: #9c7a5b;
    --sky-soft: #9fb6d6;
    --sky-pale: #dfe6f0;
    --blossom-white: #f7f3ef;
    --text-light: #ffffff;
  }
  * { box-sizing: border-box; margin: 0; padding: 0; }
  html, body {
    width: 1200px; height: 900px; overflow: hidden;
    background: var(--page-bg);
    font-family: "Open Sans", Arial, sans-serif;
  }
  .stage { position: relative; width: 1200px; height: 900px; }
  .card {
    position: absolute; top: 302px;
    width: 520px; height: 297px;
    overflow: hidden;
    box-shadow: 0 6px 18px rgba(0,0,0,0.16);
  }
  .card--back { left: 60px; }
  .card--front { left: 620px; background: var(--card-cream); }

  /* back side */
  .blossom-photo {
    position: absolute; inset: 0;
    background:
      radial-gradient(ellipse at 75% 20%, var(--blossom-white) 0%, rgba(247,243,239,0.85) 28%, rgba(247,243,239,0) 55%),
      radial-gradient(ellipse at 35% 55%, rgba(238,236,240,0.9) 0%, rgba(238,236,240,0) 45%),
      linear-gradient(160deg, var(--sky-soft) 0%, var(--sky-pale) 60%, var(--sky-soft) 100%);
  }
  .back-brand {
    position: absolute; left: 70px; top: 172px;
    display: flex; align-items: center; gap: 12px;
    color: var(--text-light);
    font-weight: 600; font-size: 26px; letter-spacing: 1px;
    text-shadow: 0 1px 3px rgba(80,60,50,0.35);
  }
  .brand-dot {
    width: 12px; height: 12px; border-radius: 50%;
    background: currentColor; flex: none;
  }

  /* front side */
  .front-brand {
    position: absolute; left: 0; right: 0; top: 62px;
    display: flex; justify-content: center; align-items: center; gap: 12px;
    color: var(--brand-rose);
    font-weight: 600; font-size: 28px; letter-spacing: 1px;
  }
  .front-rule {
    position: absolute; left: 0; right: 0; top: 166px;
    height: 4px; background: var(--rule-brown);
  }
  .contact-band {
    position: absolute; left: 0; right: 0; top: 178px; bottom: 0;
    background: var(--band-rose);
    color: var(--text-light);
  }
  .contact-list {
    position: absolute; right: 205px; top: 16px;
    list-style: none; text-align: right;
    font-size: 14px; line-height: 25px;
  }
  .contact-list li { display: flex; justify-content: flex-end; align-items: center; gap: 8px; }
  .contact-list svg { width: 12px; height: 12px; flex: none; }
  .holder-name {
    position: absolute; right: 30px; top: 14px;
    font-weight: 700; font-size: 17px; line-height: 25px;
  }
</style>
</head>
<body>
<main class="stage">

  <section class="card card--back" aria-label="Card back">
    <div class="blossom-photo" role="img" aria-label="Photograph of white almond blossoms against a soft blue sky"></div>
    <div class="back-brand"><span class="brand-dot"></span>Willow Creek Gatherings</div>
  </section>

  <section class="card card--front" aria-label="Card front">
    <div class="front-brand"><span class="brand-dot"></span>Willow Creek Gatherings</div>
    <div class="front-rule"></div>
    <div class="contact-band">
      <ul class="contact-list">
        <li>530-817-4362
          <svg viewBox="0 0 24 24" aria-hidden="true"><path fill="currentColor" d="M6.6 10.8a15 15 0 0 0 6.6 6.6l2.2-2.2a1 1 0 0 1 1-.25 11.4 11.4 0 0 0 3.6.57 1 1 0 0 1 1 1V20a1 1 0 0 1-1 1A17 17 0 0 1 3 4a1 1 0 0 1 1-1h3.5a1 1 0 0 1 1 1c0 1.25.2 2.45.57 3.6a1 1 0 0 1-.25 1z"/></svg>
        </li>
        <li>willowcgather@mailbox.test
          <svg viewBox="0 0 24 24" aria-hidden="true"><path fill="currentColor" d="M2 5h20v14H2z"/><path fill="none" stroke="#c48f9d" stroke-width="2" d="M2 5l10 8 10-8"/></svg>
        </li>
        <li>www.willowcreekgatherings.test
          <svg viewBox="0 0 24 24" aria-hidden="true"><circle cx="12" cy="12" r="10" fill="currentColor"/><path fill="none" stroke="#c48f9d" stroke-width="1.6" d="M2 12h20M12 2c3 3 3 17 0 20M12 2c-3 3-3 17 0 20"/></svg>
        </li>
      </ul>
      <p class="holder-name">Maren Lockwood</p>
    </div>
  </section>

</main>
</body>
</html>
```